Accounting firm needing business card / letterhead designed
Marcus L. Trenholm, CPA
marcus@veltrowledger.com
www.veltrowledger.com
842 E Alder Ave Harwell Springs, NV 43827
555-562-0974

```html
<!DOCTYPE html>
<html lang="en">
<head>
<meta charset="utf-8">
<title>Veltro Ledger — Business Card</title>
<link rel="stylesheet" href="https://fonts.googleapis.com/css2?family=Barlow+Semi+Condensed:wght@400;500;600&display=swap">
<style>
  :root {
    --backdrop: #dcdcdc;
    --card-white: #f6f6f6;
    --card-white-shade: #ececec;
    --navy: #1f1552;
    --green: #5fb22c;
    --green-deep: #55a526;
    --ink: #1a1a1a;
  }
  * { margin: 0; padding: 0; box-sizing: border-box; }
  html, body {
    width: 1200px; height: 576px; overflow: hidden;
    background: var(--backdrop);
    font-family: "Barlow Semi Condensed", Arial, sans-serif;
  }
  .canvas { position: relative; width: 1200px; height: 576px; }
  .card {
    position: absolute; width: 484px; height: 292px; border-radius: 12px;
    box-shadow: 0 2px 4px rgba(0,0,0,0.18);
  }
  .card--front {
    left: 82px; top: 140px;
    background: linear-gradient(160deg, var(--card-white) 0%, var(--card-white-shade) 100%);
  }
  .card--back {
    left: 602px; top: 138px;
    background: linear-gradient(160deg, #67ba2e 0%, var(--green-deep) 100%);
  }
  .holder-name {
    position: absolute; left: 29px; top: 36px;
    font-size: 20px; font-weight: 600; line-height: 24px;
    color: var(--navy); letter-spacing: 0.1px;
  }
  .holder-name .credential { color: var(--green); }
  .contact-list { position: absolute; left: 29px; top: 67px; list-style: none; }
  .contact-list li {
    display: flex; align-items: center; height: 15.5px;
    font-size: 12.5px; font-weight: 400; color: var(--ink);
  }
  .contact-list svg { width: 11px; height: 9px; margin-right: 13px; fill: var(--green); }
  .address {
    position: absolute; left: 29px; top: 118px;
    font-size: 12.5px; font-weight: 400; line-height: 16px; color: var(--ink);
  }
  .brand {
    position: absolute; display: flex; align-items: center; gap: 10px;
  }
  .card--front .brand { left: 31px; top: 219px; }
  .card--back .brand { right: 30px; top: 221px; }
  .brand-mark { width: 13px; height: 13px; background: var(--green); }
  .card--back .brand-mark { background: var(--navy); }
  .brand-name {
    font-size: 27px; font-weight: 600; color: var(--navy);
    letter-spacing: 1px; line-height: 28px;
  }
</style>
</head>
<body>
<main class="canvas">
  <section class="card card--front" aria-label="Business card front">
    <h1 class="holder-name">Marcus L. Trenholm, <span class="credential">CPA</span></h1>
    <ul class="contact-list">
      <li>
        <svg viewBox="0 0 12 10" aria-hidden="true"><path d="M1 3 C1 1 3 0.5 6 0.5 S11 1 11 3 L8.5 3.6 L8 2.5 H4 L3.5 3.6 Z M3 4.5 H9 L10.5 9.5 H1.5 Z"/></svg>
        555-562-0974
      </li>
      <li>
        <svg viewBox="0 0 12 10" aria-hidden="true"><path d="M0.5 1 H11.5 V9 H0.5 Z M1.3 1.8 L6 5.6 L10.7 1.8" stroke="#f6f6f6" stroke-width="0.9"/></svg>
        marcus@veltrowledger.com
      </li>
      <li>
        <svg viewBox="0 0 12 12" aria-hidden="true"><circle cx="6" cy="6" r="5.5"/><path d="M0.5 6 H11.5 M6 0.5 V11.5 M1.5 3.3 H10.5 M1.5 8.7 H10.5" stroke="#f6f6f6" stroke-width="0.8" fill="none"/><ellipse cx="6" cy="6" rx="2.4" ry="5.5" stroke="#f6f6f6" stroke-width="0.8" fill="none"/></svg>
        www.veltrowledger.com
      </li>
    </ul>
    <p class="address">842 E Alder Ave Harwell Springs, NV 43827</p>
    <div class="brand">
      <span class="brand-mark" aria-hidden="true"></span>
      <span class="brand-name">VELTRO LEDGER</span>
    </div>
  </section>

  <section class="card card--back" aria-label="Business card back">
    <div class="brand">
      <span class="brand-mark" aria-hidden="true"></span>
      <span class="brand-name">VELTRO LEDGER</span>
    </div>
  </section>
</main>
</body>
</html>
```